One of a Kind Clean Business Card

We need to design a new business card template for our company. Our company designs and produced merchandising displays. You can see a sample of what we produce on our site www.qorvanexhibits.net. I have uploaded our logo in vector format, as well as a picture of our current business cards. We want a totally different look. We want simple and clean, looking forward to seeing what people create.
Updates

I would like to update the address for Qorvan Display Group Inc. 518 E Tollmere Ln Arlington Heights, IL 60017 Would also note. No QR codes

Industry/Entity Type

Business

Contact Information for Business Card

Need a 1 sided business card designed.

Font styles to use
Serif

Requirements
Must have
• Easy to view; Clean Design
Nice to have
• Features that promote engineering and creativity
Should not have
• Too much clutter, keep it simple

```html
<!DOCTYPE html>
<html lang="en">
<head>
<meta charset="utf-8">
<title>Qorvan Display Group Inc. – Business Card</title>
<link rel="stylesheet" href="https://fonts.googleapis.com/css2?family=Work+Sans:wght@200;400;600&display=swap">
<style>
  :root {
    --page-bg: #ecebe9;
    --card-bg: #ffffff;
    --ink: #2b2b2b;
    --maroon: #7a2630;
    --watermark: #ecebeb;
  }
  * { box-sizing: border-box; margin: 0; padding: 0; }
  html, body {
    width: 1200px; height: 1000px; overflow: hidden;
    background: var(--page-bg);
    font-family: "Work Sans", Arial, sans-serif;
  }
  .card {
    position: absolute; left: 75px; top: 200px;
    width: 1050px; height: 600px;
    background: var(--card-bg);
    box-shadow: 0 8px 30px rgba(0,0,0,0.12);
    overflow: hidden;
  }
  .holder-name {
    position: absolute; left: 90px; top: 70px;
    font-size: 40px; font-weight: 600; letter-spacing: 1px;
    color: var(--ink); text-transform: uppercase;
  }
  .brand {
    position: absolute; right: 90px; top: 150px;
    display: flex; align-items: center; gap: 14px;
  }
  .brand-square { width: 22px; height: 22px; background: var(--ink); }
  .brand-name { font-size: 32px; font-weight: 400; color: var(--ink); }
  .watermark {
    position: absolute; right: 70px; bottom: 40px;
    font-size: 190px; font-weight: 200; color: var(--watermark);
    line-height: 1; letter-spacing: -4px;
  }
  .details {
    position: absolute; left: 90px; top: 255px;
    font-size: 23px; line-height: 1.35; color: var(--ink);
  }
  .company { color: var(--maroon); font-weight: 600; }
  .address { margin-bottom: 22px; }
  .contact-list { list-style: none; }
  .contact-list li { display: flex; align-items: center; gap: 16px; }
  .contact-list svg { width: 20px; height: 20px; fill: var(--maroon); flex: none; }
  .web-domain { color: var(--maroon); }
  .footer-band {
    position: absolute; left: 0; bottom: 0; width: 100%; height: 20px;
    background: var(--maroon);
  }
  .footer-band::before {
    content: ""; position: absolute; left: 0; top: -8px; width: 100%; height: 3px;
    background: var(--maroon); opacity: 0.5;
  }
</style>
</head>
<body>
  <div class="card">
    <h1 class="holder-name">Dale Harrow</h1>

    <div class="brand">
      <span class="brand-square"></span>
      <span class="brand-name">Qorvan Display Group Inc.</span>
    </div>

    <div class="watermark" aria-hidden="true">Qorvan</div>

    <div class="details">
      <div class="company">Qorvan Display Group Inc.</div>
      <div class="address">518 E Tollmere Ln<br>Arlington Heights, IL 60017</div>
      <ul class="contact-list">
        <li>
          <svg viewBox="0 0 24 24" aria-hidden="true"><path d="M3 9c0-3 4-5 9-5s9 2 9 5v2h-5V9c-2-1-6-1-8 0v2H3zM6 12h12l2 8H4z"/></svg>
          815-555-0142
        </li>
        <li>
          <svg viewBox="0 0 24 24" aria-hidden="true"><path d="M6.6 10.8a15 15 0 0 0 6.6 6.6l2.2-2.2c.3-.3.7-.4 1-.2 1.1.4 2.3.6 3.6.6.6 0 1 .4 1 1V20c0 .6-.4 1-1 1A17 17 0 0 1 3 4c0-.6.4-1 1-1h3.5c.6 0 1 .4 1 1 0 1.3.2 2.5.6 3.6.1.3 0 .7-.2 1z"/></svg>
          312-555-0187
        </li>
        <li>
          <svg viewBox="0 0 24 24" aria-hidden="true"><path d="M2 5h20v14H2zM4 7v.5l8 5 8-5V7l-8 5z"/></svg>
          dharrow@qorvanexhibits.net
        </li>
        <li>
          <svg viewBox="0 0 24 24" aria-hidden="true"><path d="M14 3a7 7 0 1 1-4.9 12l-5.4 5.4-1.4-1.4 5.4-5.4A7 7 0 0 1 14 3zm0 2a5 5 0 1 0 0 10 5 5 0 0 0 0-10z"/></svg>
          <span>www.<span class="web-domain">qorvanexhibits</span>.net</span>
        </li>
      </ul>
    </div>

    <div class="footer-band"></div>
  </div>
</body>
</html>
```